indépendant en tant que Massothérapeute et Préparateur Mental, j'ai besoin de ...

Massothérapeute et préparateur mental indépendant, je recherche une carte de visite sobre et dynamique, sans images liées au massage ou à la préparation mentale mais intégrant mon logo. Les couleurs que j'aime bien sont : Blanc, gris, anthracite, noir et jaune

Contact Information for Business Card

carte de préférence Horizontale
neutre qui puisse toucher le deux domaines Massothérapie et préparation mentale

Requirements
Must have
• mon projet doit intégrer au recto:
LOGO
Loïc Bardèze
078 513 26 48
info@loicbardeze.ch
et éventuellement www.loicbardeze.ch

et au verso les deux adresses:

Chemin des Ormilles 7B
1400 Yverdon-les-Bains

Route de la Gravière 9
1700 Fribourg

Should not have
• mon projet ne doit pas contenir d'image en liens avec le massage ni la préparation mentale.

```html
<!DOCTYPE html>
<html lang="fr">
<head>
<meta charset="utf-8">
<title>Loïc Bardèze – Carte de visite</title>
<link rel="stylesheet" href="https://fonts.googleapis.com/css2?family=Roboto:wght@400;500&display=swap">
<style>
  :root {
    --bg: #8a8a8a;
    --paper: #ffffff;
    --ink: #231f20;
    --ink-soft: #3a3a3a;
    --band: #231f20;
    --rule-grey: #9a9a9e;
    --metal: #b9b3b6;
    --metal-dim: #6f6a6d;
  }
  * { box-sizing: border-box; margin: 0; padding: 0; }
  html, body { width: 1200px; height: 1200px; overflow: hidden; }
  body {
    background: var(--bg);
    font-family: "Roboto", Arial, sans-serif;
    position: relative;
  }
  .card {
    position: absolute;
    left: 262px;
    width: 686px;
    height: 391px;
    border-radius: 22px;
    overflow: hidden;
  }
  .card--front { top: 166px; background: var(--paper); color: var(--ink); }
  .card--back  { top: 654px; background: var(--band); }

  .brand {
    position: absolute;
    left: 59px;
    top: 184px;
    display: flex;
    align-items: center;
    gap: 12px;
  }
  .brand__mark {
    width: 34px; height: 34px;
    border-radius: 50%;
    background: var(--ink);
    flex: none;
  }
  .brand__name { font-size: 24px; font-weight: 500; line-height: 1; }
  .brand__role {
    font-size: 9px;
    letter-spacing: 0.6px;
    text-transform: uppercase;
    margin-top: 4px;
  }

  .divider {
    position: absolute;
    left: 387px; top: 111px;
    width: 2px; height: 167px;
    background: var(--ink);
  }
  .contact { position: absolute; left: 409px; top: 108px; }
  .contact__name { font-size: 23px; font-weight: 500; margin-bottom: 14px; }
  .contact__address { font-size: 14.5px; line-height: 19px; color: var(--ink-soft); margin-bottom: 6px; }
  .contact__line {
    display: flex; align-items: center; gap: 9px;
    font-size: 14.5px; line-height: 20px; color: var(--ink-soft);
  }
  .contact__line svg { width: 12px; height: 12px; fill: var(--ink); }

  .footer-band { position: absolute; left: 0; bottom: 0; width: 686px; height: 40px; }
  .footer-band__url {
    position: absolute; left: 464px; bottom: 9px;
    color: #ffffff; font-size: 14.5px; letter-spacing: 0.3px;
  }

  .back-brand {
    position: absolute; left: 0; right: 0; top: 168px;
    display: flex; justify-content: center; align-items: center; gap: 16px;
    color: var(--metal);
  }
  .back-brand__mark { width: 46px; height: 46px; background: var(--metal); border-radius: 50%; }
  .back-brand__name { font-size: 34px; font-weight: 500; line-height: 1; }
  .back-brand__role {
    font-size: 11px; letter-spacing: 1px; text-transform: uppercase;
    color: var(--metal-dim); margin-top: 6px;
  }
</style>
</head>
<body>
  <section class="card card--front">
    <div class="brand">
      <span class="brand__mark"></span>
      <div>
        <div class="brand__name">Loïc Bardèze</div>
        <div class="brand__role">Massothérapeute / Préparateur Mental</div>
      </div>
    </div>

    <div class="divider"></div>

    <div class="contact">
      <div class="contact__name">Loïc Bardèze</div>
      <p class="contact__address">Chemin des Ormilles 7B<br>1400 Yverdon-les-Bain</p>
      <p class="contact__address">Route de la Gravière 9<br>1700 Fribourg</p>
      <div class="contact__line">
        <svg viewBox="0 0 24 24"><path d="M6.6 10.8a15.1 15.1 0 0 0 6.6 6.6l2.2-2.2a1 1 0 0 1 1-.25 11.4 11.4 0 0 0 3.6.57 1 1 0 0 1 1 1V20a1 1 0 0 1-1 1A17 17 0 0 1 3 4a1 1 0 0 1 1-1h3.5a1 1 0 0 1 1 1c0 1.25.2 2.45.57 3.57a1 1 0 0 1-.25 1z"/></svg>
        <span>078 513 26 48</span>
      </div>
      <div class="contact__line">
        <svg viewBox="0 0 24 24"><path d="M2 5h20v14H2z M2 5l10 8 10-8" fill="var(--ink)" stroke="#fff" stroke-width="1.6"/></svg>
        <span>info@loicbardeze.ch</span>
      </div>
    </div>

    <svg class="footer-band" viewBox="0 0 686 40" aria-hidden="true">
      <path d="M0 16 H408 Q420 16 428 11 L440 4 Q446 0 456 0 H686 V40 H0 Z" fill="var(--paper)"/>
      <path d="M0 16 H408 Q418 16 425 12 L428 11 L430 14 Q421 20 408 20 H0 Z" fill="var(--rule-grey)"/>
      <path d="M420 40 Q428 24 440 10 Q448 0 460 0 H686 V40 Z" fill="var(--band)"/>
    </svg>
    <span class="footer-band__url">www.loicbardeze.ch</span>
  </section>

  <section class="card card--back">
    <div class="back-brand">
      <span class="back-brand__mark"></span>
      <div>
        <div class="back-brand__name">Loïc Bardèze</div>
        <div class="back-brand__role">Massothérapeute / Préparateur Mental</div>
      </div>
    </div>
  </section>
</body>
</html>
```